Ductless Mini Split Business Website

Copper Fern Services is looking to design an eye catching educational website about installing Ductless mini splits.

Similar to this company.
https://www.halvikstream.com/

Coding

Coded - Design and coding required

```html
<!DOCTYPE html>
<html lang="en">
<head>
<meta charset="utf-8">
<title>Copper Fern Services – Ductless Experts</title>
<link rel="stylesheet" href="https://fonts.googleapis.com/css2?family=Lato:wght@400;700;900&display=swap">
<style>
:root{
  --yellow:#f7c600;
  --yellow-deep:#e0a800;
  --ink:#151515;
  --text:#333333;
  --muted:#555555;
  --paper:#ffffff;
  --mist:#f2f2f2;
  --line:#dddddd;
}
*{margin:0;padding:0;box-sizing:border-box}
html,body{width:1200px;height:4800px;overflow:hidden}
body{position:relative;background:var(--paper);font-family:'Lato',sans-serif;color:var(--text)}
.abs{position:absolute}
.btn{position:absolute;background:var(--yellow);color:var(--ink);font-weight:900;font-size:17px;display:flex;align-items:center;justify-content:center;letter-spacing:.3px}

/* header */
.brand{left:75px;top:22px;width:230px;display:flex;align-items:center;gap:12px}
.brand-mark{width:34px;height:34px;border-radius:50%;background:var(--yellow)}
.brand-name{font-weight:900;font-size:22px;color:var(--ink);line-height:1.1}
.callus{right:70px;top:28px;font-size:23px;font-weight:900;color:#444}
.callus span{color:var(--yellow-deep)}
.nav{top:82px;left:436px;display:flex;height:33px;font-size:15px;font-weight:700;color:var(--ink)}
.nav a{display:flex;align-items:center;padding:0 22px;color:inherit;text-decoration:none}
.nav a.active{background:var(--yellow)}

/* hero */
.hero{left:0;top:127px;width:1200px;height:830px}
.hero-title{left:78px;top:300px}
.hero-title .big{display:inline-block;background:var(--yellow);font-size:72px;font-weight:900;line-height:72px;color:var(--ink);padding:0 6px}
.hero-title .mid{display:inline-block;background:var(--yellow);font-size:52px;font-weight:900;line-height:54px;color:var(--ink);padding:0 6px;margin-top:4px}
.hero-title .sub{font-size:36px;font-weight:900;color:#fff;margin-top:8px;text-shadow:0 2px 6px rgba(0,0,0,.35)}

/* feature blocks */
.feature-title{font-size:34px;font-weight:900;color:#fff;line-height:38px}
.feature-copy{font-size:14px;line-height:29px;color:#e6e6e6;width:470px;margin-top:20px}

/* services */
.services{left:0;top:1611px;width:1200px;height:560px;background:var(--mist)}
.svc-card{position:absolute;width:244px;height:170px;background:#fff;box-shadow:0 3px 8px rgba(0,0,0,.18);text-align:center;padding-top:18px}
.svc-card svg{width:80px;height:66px}
.svc-card h4{font-size:17px;font-weight:900;color:var(--ink);margin-top:10px}
.svc-card p{font-size:14px;line-height:22px;color:var(--muted);margin-top:2px}
.sec-title{font-size:33px;font-weight:900;color:var(--ink)}
.sec-copy{font-size:14px;line-height:29px;color:var(--muted);width:480px;margin-top:20px}

/* testimonials */
.testi-title{top:2985px;width:1200px;text-align:center;font-size:31px;font-weight:900;color:#fff}
.quote{width:420px;text-align:center;font-size:16px;line-height:28px;color:#fff}
.avatar{width:82px;height:82px;border-radius:50%;background:linear-gradient(#d9d4cc,#a89f95);border:3px solid #fff}
.name{font-size:17px;font-weight:900;color:var(--yellow);text-align:center;width:240px}

/* blog */
.blog-title{top:3474px;width:1200px;text-align:center;font-size:32px;font-weight:900;color:var(--ink)}
.post{position:absolute;top:3534px;width:330px;height:397px;background:#fff;box-shadow:0 3px 10px rgba(0,0,0,.18);text-align:center}
.post-img{height:201px;border-bottom:5px solid var(--yellow)}
.post h3{font-size:18px;font-weight:900;color:var(--ink);line-height:25px;margin:28px 20px 0}
.post p{font-size:14px;line-height:24px;color:var(--muted);margin:6px 26px 0}

/* contact */
.contact-card{left:164px;top:4039px;width:872px;height:423px;background:#fff;box-shadow:0 3px 12px rgba(0,0,0,.2)}
.contact-title{top:4080px;width:1200px;text-align:center;font-size:33px;font-weight:900;color:var(--ink)}
.field{left:194px;width:393px;height:41px;background:#f2f2f2;border:1px solid #e2e2e2;font-size:12px;font-weight:900;color:var(--ink);padding:13px 14px}

/* footer */
.foot-col{font-size:14px;line-height:30px;color:#ddd}
.foot-col h5{font-size:16px;font-weight:900;color:var(--yellow);margin-bottom:4px;line-height:24px}
.social{display:flex;gap:14px}
.social i{display:block;width:20px;height:20px;border-radius:50%;background:#fff}
</style>
</head>
<body>

<!-- header -->
<div class="abs brand"><span class="brand-mark"></span><span class="brand-name">Copper Fern<br>Services</span></div>
<div class="abs callus">CALL US TODAY: <span>1-800-555-0148</span></div>
<nav class="abs nav">
  <a class="active">HOME</a><a>ABOUT US</a><a>SERVICES</a><a>BLOG</a><a>FAQ</a><a>BLOG</a><a>CONTACT US</a>
</nav>

<!-- hero -->
<svg class="abs hero" viewBox="0 0 1200 830" role="img" aria-label="Technician cleaning the filter of a wall-mounted ductless air conditioner">
  <defs>
    <linearGradient id="heroFill" x1="0" y1="0" x2="1" y2="1">
      <stop offset="0" stop-color="#d9d6d0"/>
      <stop offset=".45" stop-color="#bfb7ab"/>
      <stop offset="1" stop-color="#8a7a66"/>
    </linearGradient>
  </defs>
  <polygon points="0,0 1200,0 1200,674 559,823 0,516" fill="url(#heroFill)"/>
  <polygon points="0,516 72,820 0,690" fill="var(--yellow)"/>
  <polygon points="70,820 1200,674 1200,700 559,830 70,830" fill="var(--yellow)"/>
  <polygon points="60,830 1200,700 1200,830" fill="#fff"/>
</svg>
<div class="abs hero-title">
  <div class="big">COPPER FERN</div><br>
  <div class="mid">SERVICES</div>
  <div class="sub">DUCTLESS EXPERETS</div>
</div>
<div class="btn" style="left:75px;top:509px;width:170px;height:44px">CONTACT US</div>

<!-- about -->
<svg class="abs" style="left:0;top:960px" width="1200" height="600" viewBox="0 960 1200 600">
  <polygon points="75,1043 800,1025 800,1500 75,1444" fill="var(--ink)"/>
  <polygon points="898,975 1140,1118 1140,1416 898,1556 656,1416" fill="var(--yellow)"/>
  <polygon points="880,969 1127,1110 1127,1410 880,1546 633,1410 633,1110" fill="#cfcac4" role="img" aria-label="Technician installing a ductless unit on a brick wall while a homeowner watches"/>
</svg>
<div class="abs" style="left:117px;top:1085px">
  <div class="feature-title">ABOUT<br>COPPER FERN SERVICES</div>
  <p class="feature-copy">Lorem ipsum dolor sit amet, consectetur adipiscing elit. Pellentesque consectetur condimentum purus non viverra aecenas tempor pellentesque consequat. Praesent eget accumsan mi, in congue dui diam vel maximus venenatis, sapien metus rhoncus leo, ut sollicitudin mi magna a magna.</p>
</div>
<div class="btn" style="left:117px;top:1345px;width:170px;height:43px">READ MORE</div>

<!-- services -->
<div class="abs services"></div>
<svg class="abs" style="left:0;top:2060px" width="1200" height="120" viewBox="0 2060 1200 120">
  <polygon points="0,2092 689,2155 1200,2068 1200,2180 0,2180" fill="#fff"/>
  <polyline points="0,2092 689,2160 1200,2068" fill="none" stroke="var(--ink)" stroke-width="9"/>
</svg>
<div class="svc-card" style="left:75px;top:1680px">
  <svg viewBox="0 0 80 66" fill="none" stroke="var(--yellow-deep)" stroke-width="3"><rect x="4" y="6" width="72" height="30" rx="4"/><line x1="12" y1="28" x2="68" y2="28"/><path d="M20 44l-4 14M32 44l-2 14M40 44v14M48 44l2 14M60 44l4 14"/></svg>
  <h4>SED SEMPER</h4><p>Nulla fringilla diam vel metus<br>nibh scelerisque</p>
</div>
<div class="svc-card" style="left:343px;top:1680px">
  <svg viewBox="0 0 80 66" fill="none" stroke="var(--yellow-deep)" stroke-width="3"><rect x="16" y="22" width="48" height="20" rx="4"/><path d="M28 4v18M52 4v18M24 4h8M48 4h8M36 42v18h8V42"/></svg>
  <h4>SED SEMPER</h4><p>Nulla fringilla diam vel metus<br>nibh scelerisque</p>
</div>
<div class="svc-card" style="left:75px;top:1872px">
  <svg viewBox="0 0 80 66" fill="none" stroke="var(--yellow-deep)" stroke-width="3"><path d="M26 26a14 14 0 0 1 28 0z"/><circle cx="40" cy="36" r="10"/><path d="M22 62c2-10 10-14 18-14s16 4 18 14"/></svg>
  <h4>SED SEMPER</h4><p>Nulla fringilla diam vel metus<br>nibh scelerisque</p>
</div>
<div class="svc-card" style="left:343px;top:1872px">
  <svg viewBox="0 0 80 66" fill="none" stroke="var(--yellow-deep)" stroke-width="3"><circle cx="40" cy="16" r="10"/><circle cx="18" cy="24" r="8"/><circle cx="62" cy="24" r="8"/><path d="M22 56c0-14 8-22 18-22s18 8 18 22zM4 54c0-10 6-16 14-16M76 54c0-10-6-16-14-16"/></svg>
  <h4>SED SEMPER</h4><p>Nulla fringilla diam vel metus<br>nibh scelerisque</p>
</div>
<div class="abs" style="left:650px;top:1722px">
  <div class="sec-title">COPPER FERN SERVICES</div>
  <p class="sec-copy">Lorem ipsum dolor sit amet, consectetur adipiscing elit. Pellentesque consectetur condimentum purus non viverra aecenas tempor pellentesque consequat. Praesent eget accumsan mi, in congue dui diam vel maximus venenatis, sapien metus rhoncus leo, ut sollicitudin mi magna a magna.</p>
</div>
<div class="btn" style="left:650px;top:1956px;width:170px;height:43px">READ MORE</div>

<!-- why choose -->
<svg class="abs" style="left:0;top:2230px" width="1200" height="610" viewBox="0 2230 1200 610">
  <polygon points="75,2318 800,2295 800,2785 75,2720" fill="var(--ink)"/>
  <polygon points="898,2255 1140,2398 1140,2696 898,2836 656,2696" fill="var(--yellow)"/>
  <polygon points="880,2245 1127,2387 1127,2687 880,2822 633,2687 633,2387" fill="#c9d3da" role="img" aria-label="Man relaxing on a sofa under a cooling ductless unit in a living room"/>
</svg>
<div class="abs" style="left:117px;top:2358px">
  <div class="feature-title">WHY CHOOSE<br>COPPER FERN SERVICES ?</div>
  <p class="feature-copy">Lorem ipsum dolor sit amet, consectetur adipiscing elit. Pellentesque consectetur condimentum purus non viverra aecenas tempor pellentesque consequat. Praesent eget accumsan mi, in congue dui diam vel maximus venenatis, sapien metus rhoncus leo, ut sollicitudin mi magna a magna.</p>
</div>
<div class="btn" style="left:117px;top:2618px;width:170px;height:43px">READ MORE</div>

<!-- testimonials -->
<svg class="abs" style="left:0;top:2890px" width="1200" height="545" viewBox="0 2890 1200 545">
  <defs>
    <linearGradient id="testiFill" x1="0" y1="0" x2="0" y2="1">
      <stop offset="0" stop-color="var(--yellow)"/>
      <stop offset=".55" stop-color="#6b5500"/>
      <stop offset="1" stop-color="#111"/>
    </linearGradient>
  </defs>
  <polygon points="0,2990 745,2897 1200,2999 1200,3316 0,3428" fill="url(#testiFill)"/>
  <polygon points="500,3390 1200,3300 1200,3328 0,3432 0,3428" fill="var(--yellow)"/>
  <polyline points="1020,3185 1050,3176 1020,3167" fill="none"/>
  <path d="M82 3160l-14 16 14 16M1046 3160l14 16-14 16" fill="none" stroke="#fff" stroke-width="4"/>
</svg>
<div class="abs testi-title">TESTIMONIALS</div>
<p class="abs quote" style="left:153px;top:3070px">“ Praesent eget accumsan mi, in congue dui. auris molestie metus in mauris mattis, nec tincidunt nibh elementum rutrum felis id augue maximus fermentum interdum leo feugiat efficitur.”</p>
<p class="abs quote" style="left:623px;top:3070px">“ Praesent eget accumsan mi, in congue dui. auris molestie metus in mauris mattis, nec tincidunt nibh elementum rutrum felis id augue maximus fermentum interdum leo feugiat efficitur.”</p>
<div class="abs avatar" role="img" aria-label="Customer portrait" style="left:322px;top:3196px"></div>
<div class="abs avatar" role="img" aria-label="Customer portrait" style="left:792px;top:3196px"></div>
<div class="abs name" style="left:243px;top:3293px">NAME HEADING</div>
<div class="abs name" style="left:713px;top:3293px">NAME HEADING</div>

<!-- blog -->
<div class="abs blog-title">BLOG POSTS</div>
<article class="post" style="left:75px">
  <div class="post-img" role="img" aria-label="Technician servicing an indoor unit" style="background:linear-gradient(#e4e4e2,#b6b1aa)"></div>
  <h3>PROIN IMPERDIET VITAE LIBER ERAT VOLUTPAT.</h3>
  <p>Liquam rutrum felis id augue maximus fermentum. Nullam magna sem, ullamcor et dictum quis</p>
</article>
<article class="post" style="left:434px">
  <div class="post-img" role="img" aria-label="Couple enjoying cool air on a sofa" style="background:linear-gradient(#eeeeee,#9a9ea5)"></div>
  <h3>PROIN IMPERDIET VITAE LIBER ERAT VOLUTPAT.</h3>
  <p>Liquam rutrum felis id augue maximus fermentum. Nullam magna sem, ullamcor et dictum quis</p>
</article>
<article class="post" style="left:796px">
  <div class="post-img" role="img" aria-label="Cleaning spray on an open air conditioner" style="background:linear-gradient(#f2f2f2,#9fa8b8)"></div>
  <h3>PROIN IMPERDIET VITAE LIBER ERAT VOLUTPAT.</h3>
  <p>Liquam rutrum felis id augue maximus fermentum. Nullam magna sem, ullamcor et dictum quis</p>
</article>

<!-- contact + footer backdrop -->
<svg class="abs" style="left:0;top:4250px" width="1200" height="550" viewBox="0 4250 1200 550">
  <polygon points="0,4505 164,4395 1036,4395 1200,4288 1200,4800 0,4800" fill="var(--ink)"/>
  <polygon points="0,4505 164,4395 164,4418 0,4530" fill="var(--yellow)"/>
  <polygon points="1036,4360 1200,4262 1200,4288 1036,4390" fill="var(--yellow)"/>
</svg>
<div class="abs contact-card"></div>
<div class="abs contact-title">CONTACT US</div>
<div class="abs field" style="top:4149px">NAME</div>
<div class="abs field" style="top:4199px">EMAIL ADDRESS</div>
<div class="abs field" style="top:4248px">PHONE</div>
<div class="abs field" style="top:4299px;height:79px">MESSAGE</div>
<div class="btn" style="left:194px;top:4397px;width:170px;height:42px">READ MORE</div>
<div class="abs" role="img" aria-label="Map of the service area" style="left:615px;top:4149px;width:398px;height:289px;background:linear-gradient(135deg,#eef1e6,#dfe6d5 55%,#e9e5d6)"></div>

<!-- footer -->
<div class="abs" style="left:168px;top:4580px;display:flex;align-items:center;gap:10px">
  <span class="brand-mark"></span><span style="font-weight:900;font-size:20px;color:var(--yellow);line-height:1.1">Copper Fern<br>Services</span>
</div>
<p class="abs" style="left:168px;top:4664px;font-size:12px;line-height:22px;color:#ccc">Copyright © 2019. Company Name.<br>All Right Reserved</p>
<div class="abs foot-col" style="left:434px;top:4515px">
  <h5>SITE MAP</h5>Home<br>About Us<br>Services<br>Blog<br>FAQ<br>Blog<br>Contact Us
</div>
<div class="abs foot-col" style="left:650px;top:4515px">
  <h5>SERVICES</h5>Praesent eget<br>Accumsan miincon<br>Mauris molestie<br>Metus in mauris mattis<br>Aliquam auctor
</div>
<div class="abs foot-col" style="left:904px;top:4515px;font-size:13px;line-height:26px">
  <h5>CONTACT INFO</h5>
  42 Larchmoor Lane<br>Brennick, K17 3TW<br>
  <span style="display:flex;align-items:center;gap:14px"><svg width="14" height="14" viewBox="0 0 24 24" fill="#ddd"><path d="M6.6 10.8a15 15 0 0 0 6.6 6.6l2.2-2.2a1 1 0 0 1 1-.25 11.4 11.4 0 0 0 3.6.6 1 1 0 0 1 1 1V20a1 1 0 0 1-1 1A17 17 0 0 1 3 4a1 1 0 0 1 1-1h3.5a1 1 0 0 1 1 1 11.4 11.4 0 0 0 .6 3.6 1 1 0 0 1-.25 1z"/></svg>1-800-555-0148</span>
  <span style="display:flex;align-items:center;gap:14px"><svg width="14" height="12" viewBox="0 0 24 18" fill="#ddd"><path d="M0 0h24v2L12 10 0 2zM0 4.5l12 8 12-8V18H0z"/></svg>hello@copperfern.example</span>
  <div class="social" style="margin-top:14px"><i></i><i></i><i></i><i></i><i></i></div>
</div>

</body>
</html>
```